FinTech company looking to revamp and expand client-facing interface for our financial models

Pellworth Engines currently has a very simple website that allows clients to interact with our financial models. We are looking to completely redesign the current site and add several extra pages to provide extra functionality. We want the design to have a modern, slick feel, that will work on both a desktop or a tablet. It should be straightforward for clients to move between different pages at any time, and clear from the layout how to interact with the more advanced features. We have included screenshots of existing pages in the attached design brief, as well as sketches of the functionality required by the new pages, but can't provide a direct link to the current site.
Target Market(s)
Professional investors that will be paying to access the interface
Industry/Entity Type
Finance
Number of Pages Required
4 page
Colors
Designer to choose colors to be used in the design.
Look and feel
Each slider illustrates characteristics of the customer's brand and the style your logo design should communicate.

```html
<!DOCTYPE html>
<html lang="en">
<head>
<meta charset="utf-8">
<title>Portfolio Builder</title>
<link href="https://fonts.googleapis.com/css2?family=Open+Sans:wght@400;600;700&family=Roboto+Condensed:wght@400;500&display=swap" rel="stylesheet">
<style>
:root{
  --navy:#0b3466;
  --teal:#006a6a;
  --black:#1b1b1b;
  --green:#13a10e;
  --red:#d01010;
  --page:#ececec;
  --row-alt:#f1f1f1;
  --text:#111;
  --muted:#555;
}
*{box-sizing:border-box;margin:0;padding:0}
html,body{width:1200px;height:1108px;overflow:hidden;background:#e6e6e6}
.stage{position:absolute;left:0;top:0;width:1300px;height:1200px;transform:scale(0.9231);transform-origin:0 0;font-family:"Open Sans",sans-serif;color:var(--text)}
.frame{position:absolute;left:15px;top:15px;width:1270px;height:1170px;background:linear-gradient(#e4e4e4,#f6f6f6 30%,#f3f3f3)}
.abs{position:absolute}
/* top bar */
.topbar{left:15px;top:15px;width:1270px;height:60px;background:#fff;box-shadow:0 4px 10px rgba(0,0,0,.08);display:flex;align-items:center}
.topbar .cell{height:60px;display:flex;align-items:center;justify-content:center;font-weight:700;font-size:14px;border-right:1px solid #e3e3e3;gap:8px}
.brand{width:181px;font-size:18px!important;letter-spacing:.3px}
.range{width:90px}
.spacer{flex:1}
.nav{font-size:13px!important;border-left:1px solid #e3e3e3;border-right:none!important}
/* titles */
.title{background:var(--navy);color:#fff;font-weight:600;text-align:center;border-radius:2px}
/* members */
.card{background:#fff;box-shadow:0 2px 8px rgba(0,0,0,.12);border-radius:3px;overflow:hidden}
.members .head{height:50px;background:var(--black);color:#fff;font-weight:600;font-size:17px;display:flex;align-items:center;justify-content:center}
.members .cols{display:flex;height:50px;background:var(--teal);color:#fff;font-size:17px;font-weight:600}
.members .cols div{flex:1;display:flex;align-items:center;justify-content:center}
.members .cols div:first-child{border-right:1px solid #3d8f8f}
.row{display:flex;height:69px;font-family:"Roboto Condensed",sans-serif;font-size:18px}
.row:nth-child(even){background:var(--row-alt)}
.row .name{flex:1;display:flex;align-items:center;padding-left:50px;gap:28px;border-right:1px solid #e2e2e2}
.row .size{flex:1;display:flex;align-items:center;justify-content:center}
.btn{display:flex;align-items:center;justify-content:center;gap:12px;color:#fff;font-weight:700;font-size:14px;border-radius:3px;height:40px}
/* sensitivities */
.sens .head{height:70px;background:var(--teal);color:#fff;font-weight:600;font-size:17px;display:flex;align-items:center;justify-content:center}
.srow{height:70px;position:relative;font-family:"Roboto Condensed",sans-serif;font-size:18px;font-weight:500}
.srow:nth-child(odd){background:var(--row-alt)}
.track{position:absolute;top:20px;width:230px;height:30px;border-radius:15px;background:linear-gradient(#fff,#e2e2e2);box-shadow:inset 0 0 0 1.5px #c9c9c9}
.fill{position:absolute;top:0;height:30px;border-radius:15px}
.fill.neg{right:0;background:linear-gradient(#e81a0c,#c51208 60%,#a30d06)}
.fill.pos{left:0;background:linear-gradient(#0fbf0f,#03a203 60%,#047c04)}
.slabel{position:absolute;top:24px}
/* chart panel */
.tabbar{left:70px;top:680px;width:1160px;height:85px;background:#eee;box-shadow:0 2px 6px rgba(0,0,0,.1)}
.tab{position:absolute;height:35px;background:#fff;font-size:13px;font-weight:700;color:#444;display:flex;align-items:center;justify-content:center}
.chartcard{left:70px;top:765px;width:1160px;height:340px;background:#fff;box-shadow:0 2px 6px rgba(0,0,0,.1);border-radius:0 0 3px 3px}
svg text{font-family:"Open Sans",sans-serif}
</style>
</head>
<body>
<div class="stage">
  <div class="frame"></div>

  <header class="abs topbar">
    <div class="cell brand">KORVA</div>
    <div class="cell range">250D</div>
    <div class="cell range">83D</div>
    <div class="cell range">42D</div>
    <div class="spacer"></div>
    <div class="cell nav" style="width:141px">
      <svg width="24" height="24" viewBox="0 0 24 24"><path d="M2 12 12 3l10 9M5 10v11h5v-6h4v6h5V10M16 5h3v4" fill="none" stroke="#111" stroke-width="2.2" stroke-linejoin="round"/></svg>MODELS</div>
    <div class="cell nav" style="width:177px">
      <svg width="26" height="26" viewBox="0 0 26 26" fill="#333"><circle cx="13" cy="13" r="3"/><g fill="none" stroke="#333" stroke-width="1.6" stroke-dasharray="2 2"><circle cx="13" cy="13" r="7"/><circle cx="13" cy="13" r="11"/></g></svg>SENSITIVITIES</div>
    <div class="cell nav" style="width:197px">
      <svg width="26" height="26" viewBox="0 0 24 24"><path d="M12 2.5l2.9 6.3 6.8.7-5.1 4.6 1.5 6.8L12 17.4l-6.1 3.5 1.5-6.8-5.1-4.6 6.8-.7z" fill="none" stroke="#111" stroke-width="1.8" stroke-linejoin="round"/></svg>FAVOURITES</div>
  </header>

  <h1 class="abs title" style="left:487px;top:115px;width:325px;height:55px;font-size:21px;line-height:55px">PORTFOLIO BUILDER</h1>

  <section class="abs card members" style="left:70px;top:190px;width:560px;height:310px">
    <div class="head">Current Members</div>
    <div class="cols"><div>Members Name</div><div>Size</div></div>
    <div class="rows">
      <div class="row"><div class="name"><svg width="26" height="26"><circle cx="13" cy="13" r="11" fill="none" stroke="#b01010" stroke-width="2"/><path d="M7 13h12" stroke="#b01010" stroke-width="2.4"/></svg>Member 1</div><div class="size">0.2</div></div>
      <div class="row"><div class="name"><svg width="26" height="26"><circle cx="13" cy="13" r="11" fill="none" stroke="#b01010" stroke-width="2"/><path d="M7 13h12" stroke="#b01010" stroke-width="2.4"/></svg>Member 2</div><div class="size">0.5</div></div>
      <div class="row"><div class="name"><svg width="26" height="26"><circle cx="13" cy="13" r="11" fill="none" stroke="#b01010" stroke-width="2"/><path d="M7 13h12" stroke="#b01010" stroke-width="2.4"/></svg>Member 3</div><div class="size">-0.3</div></div>
    </div>
  </section>

  <div class="abs btn" style="left:70px;top:520px;width:195px;background:var(--navy)">
    <svg width="24" height="24"><circle cx="12" cy="12" r="10" fill="none" stroke="#fff" stroke-width="1.6"/><path d="M12 6v12M6 12h12" stroke="#fff" stroke-width="1.6"/></svg>ADD A MEMBER</div>
  <div class="abs btn" style="left:275px;top:520px;width:200px;background:var(--green)">
    <svg width="24" height="22"><path d="M2 12l7 7L22 3" fill="none" stroke="#fff" stroke-width="3.4"/></svg>SAVE PORTFOLIO</div>

  <section class="abs card sens" style="left:670px;top:190px;width:560px;height:350px">
    <div class="head">Sensitivities</div>
    <div class="srow" style="background:#fff"><span class="slabel" style="left:30px">A</span><div class="track" style="left:50px"><div class="fill neg" style="width:130px"></div></div></div>
    <div class="srow" style="background:var(--row-alt)"><span class="slabel" style="left:30px">B</span><div class="track" style="left:50px"><div class="fill neg" style="width:70px"></div></div></div>
    <div class="srow" style="background:#fff"><div class="track" style="left:280px"><div class="fill pos" style="width:130px"></div></div><span class="slabel" style="left:522px">C</span></div>
    <div class="srow" style="background:var(--row-alt)"><div class="track" style="left:280px"><div class="fill pos" style="width:170px"></div></div><span class="slabel" style="left:522px">D</span></div>
  </section>

  <h2 class="abs title" style="left:487px;top:620px;width:325px;height:40px;font-size:17px;line-height:40px">Properties of Collection</h2>

  <div class="abs tabbar">
    <div class="tab" style="left:55px;top:50px;width:155px;background:var(--navy);color:#fff">CHART</div>
    <div class="tab" style="left:215px;top:50px;width:90px">#1</div>
    <div class="tab" style="left:310px;top:50px;width:90px">#2</div>
    <div class="tab" style="left:405px;top:45px;width:90px;height:40px">#3</div>
    <div class="tab" style="left:500px;top:40px;width:90px;height:45px;background:var(--black);color:#fff;border-radius:3px 3px 0 0">#4</div>
  </div>

  <div class="abs chartcard"></div>

  <svg class="abs" style="left:0;top:0" width="1300" height="1200" viewBox="0 0 1300 1200" role="img" aria-label="Scatter chart of collection properties from July 2018 to July 2019">
    <g stroke="#ececec" stroke-width="1">
      <path d="M182 812V1015M325 812V1015M466 812V1015M606 812V1015M742 812V1015M883 812V1015M1022 812V1015"/>
      <path d="M155 828H1075M155 865H1075M155 903H1075M155 940H1075M155 978H1075"/>
    </g>
    <path d="M155 1015H1077" stroke="#555" stroke-width="1"/>
    <g font-size="11" fill="#555" text-anchor="end">
      <text x="150" y="832">100</text><text x="150" y="869">80</text><text x="150" y="907">60</text><text x="150" y="944">40</text><text x="150" y="982">20</text><text x="150" y="1019">0</text>
    </g>
    <g font-size="11" fill="#555" text-anchor="middle">
      <text x="182" y="1040">Jul 2018</text><text x="325" y="1040">Sep 2018</text><text x="466" y="1040">Nov 2018</text><text x="606" y="1040">Jan 2019</text><text x="742" y="1040">Mar 2019</text><text x="883" y="1040">May 2019</text><text x="1022" y="1040">Jul 2019</text>
    </g>
    <g fill="none" stroke-linecap="round" stroke-width="7">
      <path stroke="#b7b83c" d="M203 828H285M287 832h0M290 840h0M294 832h0M298 843h0M302 832h0M308 830h0M312 836h0M316 830h0M320 838h0M324 832h0M330 836h0M334 840h0M336 893h0M338 925h0M342 942h0M346 932h0M350 905h0M354 945h0M357 928h0M362 962h0M364 928h0M367 938h0M370 922h0M374 930h0M378 930h0M380 888h0M383 893h0M386 870h0M390 860h0M394 858h0M398 855h0M400 830h0M404 836h0M408 832h0M410 886h0M412 905h0M415 898h0M418 906h0M421 920h0M425 915h0M428 910h0M431 990h0M435 985h0M440 978h0M444 962h0M447 990h0M450 972h0M454 984h0M458 970h0M462 1000h0M466 1010h0M470 1008h0M474 1004h0M478 1005h0M483 996h0M486 1002h0M490 992h0M494 962h0M498 990h0M502 978h0M506 956h0M510 968h0M514 950h0M518 968h0M522 955h0M526 912h0M530 900h0M534 920h0M538 903h0M541 830h0M546 835h0M551 828h0M556 838h0M560 840h0M566 838h0M572 848h0M576 1000h0M580 1005h0M590 1000h0M594 1005h0M598 1000h0M602 996h0M606 988h0M610 998h0M614 992h0M618 996h0M622 990h0M626 996h0M630 1000h0M634 1002h0M638 996h0M642 972h0M646 966h0M650 962h0M654 890h0M657 928h0M660 942h0M665 890h0M670 855h0M674 848h0M680 855h0M686 848h0M690 904h0M694 970h0M698 975h0M702 984h0M706 860h0M710 882h0M714 870h0M718 886h0M720 928h0M722 837h0M728 845h0M732 852h0M736 843h0M740 838h0M744 830h0M748 842h0M752 836h0M760 829H1020"/>
      <path stroke="#3c6db0" d="M203 893h0M205 840h0M210 832h0M218 840h0M222 908h0M227 942h0M232 937h0M236 955h0M238 970h0M241 950h0M246 958h0M250 962h0M252 944h0M256 905h0M259 930h0M263 940h0M266 930h0M269 908h0M272 930h0M274 970h0M280 968h0M284 962h0M286 930h0M289 945h0M293 940h0M296 958h0M300 970h0M303 958h0M306 962h0M310 970h0M313 960h0M316 970h0M320 966h0M323 968h0M332 975h0M336 992h0M340 996h0M344 994h0M348 988h0M352 994h0M356 990h0M361 996h0M364 988h0M368 984h0M372 990h0M376 990h0M380 972h0M383 964h0M386 966h0M392 957h0M396 962h0M400 970h0M403 960h0M408 980h0M412 975h0M416 970h0M420 982h0M424 976h0M428 972h0M432 1011h0M436 1010h0M440 982h0M444 978h0M446 1002h0M450 994h0M455 997h0M460 958h0M463 885h0M468 858h0M472 852h0M476 858h0M479 841h0M482 866h0M487 868h0M490 851h0M494 992h0M496 980h0M500 986h0M503 974h0M506 983h0M510 968h0M514 965h0M520 955h0M525 978h0M528 945h0M533 933h0M539 934h0M541 848h0M546 843h0M551 836h0M556 832h0M562 832h0M570 832h0M576 828h0M592 828H1025"/>
      <path stroke="#2e9a2e" d="M1000 1012h10"/>
    </g>
    <text x="1132" y="830" font-size="11" fill="#333" style="font-family:serif">Names</text>
    <g>
      <circle cx="1114" cy="826" r="3.5" fill="#8fb5db"/><circle cx="1114" cy="845" r="3.5" fill="#f4b183"/><circle cx="1114" cy="864" r="3.5" fill="#2e9a2e"/><circle cx="1114" cy="883" r="3.5" fill="#d88080"/><circle cx="1114" cy="901" r="3.5" fill="#b7a0d6"/><circle cx="1114" cy="920" r="3.5" fill="#b89a8a"/><circle cx="1114" cy="938" r="3.5" fill="#eeaacc"/><circle cx="1114" cy="957" r="3.5" fill="#b5b5b5"/><circle cx="1114" cy="975" r="3.5" fill="#b7b83c"/><circle cx="1114" cy="994" r="3.5" fill="#9ee0e6"/><circle cx="1114" cy="1013" r="3.5" fill="#3c6db0"/>
    </g>
  </svg>
</div>
</body>
</html>
```